Plenko - Shoe Fitting App : Foot scanning app, 3D reconstruction and Fit recommandation.

We are a startup that has developed a 3D scanning App that compares the 3d reconstructed foot to the 3D Last (mould) of a shoe to find the best match and recommend a shoe size with a graphical representation of the fit on a reconstructed foot without texturing. The challenge of this app is to have a simple and intuitive onboarding of the user with clean and crisp ui and a simple tutorial for foot scanning. 3D representation of the fit is also key. What you see is what you feel is what we would like to achieve.

Target Market(s)

Sneaker Brands and athletic shoes brands

Industry/Entity Type

Footwear

Font styles to use
Other font styles liked:
• Oswald or Droid Serif

Colors
0094D4
00A9DD
6FCCEA
C7EBF8
E9F6FB

Requirements
Must have
• Simple intuitive UI to onboard the customer to scan his bare foot (please look at attached image on how to scan the foot). You must flip your phone so that the screen is facing your foot. Start at 40cm distance form the front of your foot and turn 360% slowly to capture the foot while you feel the aptic of the iPhone. That needs to be presented with a simple animation that the user can easily understand and skip if he is a returning customer and knows how to do that. the rest of the UI is to present the result of the scanned foot for the user to use to get his fit and size. The other must have is the final result screen. Where the user will a representation of the foot (snug, loose ) of different predefined areas of the foot so he can choose the fit that he likes and not necessarily the size that we suggest. Must match website design (https://www.plenko.example)
Nice to have
• An animation of the whole process (scan-compare 3d foot with 3d shoe last(or mould) and get the 3D result of the best fit + associated size. Optionaly, an option to play with your foot and transform it (avatar like with accessories and colours)
Should not have
• Too many colours. Too much text. No gender type. No race type.

```html
<!DOCTYPE html>
<html lang="en">
<head>
<meta charset="utf-8">
<title>Plenko – Onboarding</title>
<link rel="stylesheet" href="https://fonts.googleapis.com/css2?family=Inter:wght@400;500;800&family=Noto+Serif:wght@400&display=swap">
<style>
  :root {
    --bg: #fde8cb;
    --ink: #152a3f;
    --black: #161616;
    --screen: #ffffff;
    --teal: #4ab5b5;
    --teal-soft: #c9ecec;
    --text: #2b2b2b;
    --muted: #7a7a7a;
    --dash: #3a3d3f;
    --button: #33383a;
  }
  * { box-sizing: border-box; margin: 0; padding: 0; }
  html, body { width: 1200px; height: 1010px; overflow: hidden; }
  body {
    background: var(--bg);
    font-family: "Inter", sans-serif;
    position: relative;
  }
  .page-title {
    position: absolute; top: 48px; left: 0; width: 1200px;
    text-align: center;
    font-weight: 800; font-size: 88px; letter-spacing: -3px;
    color: var(--ink); line-height: 1;
  }
  .screen {
    position: absolute; top: 255px;
    width: 176px; height: 367px;
    border-radius: 26px;
    background: var(--screen);
    overflow: hidden;
  }
  .screen--splash {
    background: var(--black);
    display: flex; align-items: center; justify-content: center;
  }
  .splash-name {
    color: #fff; font-weight: 800; font-size: 30px; letter-spacing: -0.5px;
  }
  .status-bar {
    position: absolute; top: 14px; left: 13px; right: 12px;
    display: flex; justify-content: space-between; align-items: center;
    font-size: 7px; font-weight: 500; color: var(--text);
  }
  .status-icons { display: flex; gap: 3px; align-items: center; }
  .skip {
    position: absolute; top: 39px; right: 17px;
    font-family: "Noto Serif", serif; font-size: 8.5px; color: var(--text);
  }
  .illustration {
    position: absolute; top: 64px; left: 28px;
    width: 124px; height: 146px;
    border-radius: 40% 55% 45% 50%;
    background: radial-gradient(ellipse at 50% 50%, var(--teal) 0%, var(--teal) 50%, var(--teal-soft) 75%, rgba(255,255,255,0) 100%);
  }
  .step-title {
    position: absolute; top: 227px; left: 10px; right: 10px;
    text-align: center;
    font-family: "Noto Serif", serif; font-size: 13.5px; line-height: 17px;
    color: var(--text);
  }
  .step-text {
    position: absolute; top: 266px; left: 12px; right: 12px;
    text-align: center;
    font-size: 6.3px; line-height: 10px; color: var(--muted);
  }
  .progress {
    position: absolute; top: 299px; left: 0; width: 100%;
    display: flex; justify-content: center; gap: 2px;
  }
  .progress span { width: 5px; height: 1.4px; background: var(--dash); }
  .progress span.is-active { width: 9px; background: var(--teal); }
  .next-button {
    position: absolute; top: 314px; left: 16px;
    width: 144px; height: 20px; border-radius: 2px;
    background: var(--button);
    color: #fff; font-size: 6.8px; font-weight: 500;
    display: flex; align-items: center; justify-content: center;
  }
  .brand-name {
    position: absolute; top: 680px; left: 0; width: 1200px;
    text-align: center;
    font-weight: 800; font-size: 190px; letter-spacing: -6px;
    color: var(--black); line-height: 1;
  }
</style>
</head>
<body>
  <h1 class="page-title">Onboarding</h1>

  <div class="screen screen--splash" style="left:110px">
    <span class="splash-name">Plenko</span>
  </div>

  <div class="screen" style="left:318px">
    <div class="status-bar"><span>9:41</span>
      <span class="status-icons"><svg width="9" height="6"><rect x="0" y="4" width="1.5" height="2"/><rect x="2.5" y="3" width="1.5" height="3"/><rect x="5" y="1.5" width="1.5" height="4.5"/><rect x="7.5" y="0" width="1.5" height="6"/></svg><svg width="8" height="6"><path d="M4 6 L1 2.5 A4.5 4.5 0 0 1 7 2.5 Z"/></svg><svg width="11" height="6"><rect x="0.5" y="0.5" width="9" height="5" rx="1.2" fill="#000"/></svg></span></div>
    <span class="skip">Skip</span>
    <div class="illustration" role="img" aria-label="Illustration of a hand switching on a light beside a glowing bulb"></div>
    <h2 class="step-title">Step 1: Ensure Proper Lighting</h2>
    <p class="step-text">Use a well-lit area to avoid shadows for an accurate scan.</p>
    <div class="progress"><span class="is-active"></span><span></span><span></span><span></span></div>
    <div class="next-button">Next</div>
  </div>

  <div class="screen" style="left:526px">
    <div class="status-bar"><span>9:41</span>
      <span class="status-icons"><svg width="9" height="6"><rect x="0" y="4" width="1.5" height="2"/><rect x="2.5" y="3" width="1.5" height="3"/><rect x="5" y="1.5" width="1.5" height="4.5"/><rect x="7.5" y="0" width="1.5" height="6"/></svg><svg width="8" height="6"><path d="M4 6 L1 2.5 A4.5 4.5 0 0 1 7 2.5 Z"/></svg><svg width="11" height="6"><rect x="0.5" y="0.5" width="9" height="5" rx="1.2" fill="#000"/></svg></span></div>
    <span class="skip">Skip</span>
    <div class="illustration" role="img" aria-label="Illustration of a person taking off a shoe and rolling up trousers"></div>
    <h2 class="step-title">Step 2: Prepare Your Feet</h2>
    <p class="step-text">Remove shoes and roll up pants for full foot visibility.</p>
    <div class="progress"><span></span><span class="is-active"></span><span></span><span></span></div>
    <div class="next-button">Next</div>
  </div>

  <div class="screen" style="left:734px">
    <div class="status-bar"><span>9:41</span>
      <span class="status-icons"><svg width="9" height="6"><rect x="0" y="4" width="1.5" height="2"/><rect x="2.5" y="3" width="1.5" height="3"/><rect x="5" y="1.5" width="1.5" height="4.5"/><rect x="7.5" y="0" width="1.5" height="6"/></svg><svg width="8" height="6"><path d="M4 6 L1 2.5 A4.5 4.5 0 0 1 7 2.5 Z"/></svg><svg width="11" height="6"><rect x="0.5" y="0.5" width="9" height="5" rx="1.2" fill="#000"/></svg></span></div>
    <span class="skip">Skip</span>
    <div class="illustration" role="img" aria-label="Illustration of a seated person holding a phone near a bare foot"></div>
    <h2 class="step-title">Step 3: Position Your Phone</h2>
    <p class="step-text">Hold your phone 40 cm away and keep it steady.</p>
    <div class="progress"><span></span><span></span><span class="is-active"></span><span></span></div>
    <div class="next-button">Next</div>
  </div>

  <div class="screen" style="left:942px">
    <div class="status-bar"><span>9:41</span>
      <span class="status-icons"><svg width="9" height="6"><rect x="0" y="4" width="1.5" height="2"/><rect x="2.5" y="3" width="1.5" height="3"/><rect x="5" y="1.5" width="1.5" height="4.5"/><rect x="7.5" y="0" width="1.5" height="6"/></svg><svg width="8" height="6"><path d="M4 6 L1 2.5 A4.5 4.5 0 0 1 7 2.5 Z"/></svg><svg width="11" height="6"><rect x="0.5" y="0.5" width="9" height="5" rx="1.2" fill="#000"/></svg></span></div>
    <span class="skip">Skip</span>
    <div class="illustration" role="img" aria-label="Illustration of hands moving a phone around a bare foot"></div>
    <h2 class="step-title">Step 4: Scan Your Foot (360° Rotation)</h2>
    <p class="step-text">Move your phone slowly around your foot for a full scan.</p>
    <div class="progress"><span></span><span></span><span></span><span class="is-active"></span></div>
    <div class="next-button">Next</div>
  </div>

  <div class="brand-name">Plenko</div>
</body>
</html>
```